Rollers & Glides.com

Vertical Business Card with focus on branding with our icon. Information on card will be logo, persons name, position, phone number, email address and website. Use the the name Marcus Pellow, position President, phone number 480.915.2267, email Marcus@rollersandglides-demo.com, website www.rollersandglides-demo.com.

```html
<!DOCTYPE html>
<html lang="en">
<head>
<meta charset="utf-8">
<title>Rollers &amp; Glides.com — Business Card</title>
<link rel="stylesheet" href="https://fonts.googleapis.com/css2?family=Fira+Sans+Condensed:wght@700&family=Roboto:wght@400;500&display=swap">
<style>
  :root {
    --backdrop: #ccd0d1;
    --paper: #f1f1ef;
    --navy: #1b2a8a;
    --ink: #2a2a2a;
    --royal: #1e4a9e;
    --white: #ffffff;
  }
  * { margin: 0; padding: 0; box-sizing: border-box; }
  html, body { width: 1200px; height: 1049px; overflow: hidden; }
  body {
    background: var(--backdrop);
    font-family: "Roboto", Arial, sans-serif;
    position: relative;
  }
  .card {
    position: absolute;
    top: 140px;
    width: 440px;
    height: 770px;
    border-radius: 3px;
  }
  .card--front { left: 140px; background: var(--paper); color: var(--ink); --accent: var(--navy); }
  .card--back  { left: 620px; background: var(--royal); color: var(--white); --accent: var(--white); }

  .brand-mark {
    position: absolute;
    left: 60px;
    top: 190px;
    display: flex;
    align-items: center;
    gap: 14px;
    font-family: "Fira Sans Condensed", sans-serif;
    font-weight: 700;
    font-size: 30px;
    color: var(--accent);
  }
  .brand-mark__dot {
    width: 54px; height: 54px;
    border-radius: 50%;
    border: 10px solid var(--accent);
  }

  .contact {
    position: absolute;
    left: 92px;
    top: 420px;
  }
  .contact__name {
    font-weight: 500;
    font-size: 24px;
    color: var(--accent);
    line-height: 1.1;
  }
  .contact__role {
    font-weight: 500;
    font-size: 19px;
    line-height: 1.3;
  }
  .contact__rule {
    width: 2px; height: 26px;
    background: var(--accent);
    margin: 14px 0 14px 2px;
    transform: rotate(90deg);
    transform-origin: 1px 13px;
    height: 22px;
  }
  .contact__list { list-style: none; }
  .contact__item {
    display: flex;
    align-items: center;
    gap: 8px;
    font-size: 18px;
    line-height: 1.55;
  }
  .contact__icon { width: 16px; height: 16px; flex: none; fill: var(--accent); }

  .wordmark {
    position: absolute;
    left: 46px;
    bottom: 46px;
    font-family: "Fira Sans Condensed", sans-serif;
    font-weight: 700;
    font-size: 40px;
    letter-spacing: 0.5px;
    color: var(--accent);
  }
</style>
</head>
<body>

<svg width="0" height="0" style="position:absolute" aria-hidden="true">
  <defs>
    <symbol id="icon-phone" viewBox="0 0 16 16">
      <path d="M3 1h3l1 4-2 1.5c.8 1.8 2.2 3.2 4 4L10.5 8.5l4 1V13c0 1-1 2-2 2C6.5 15 1 9.5 1 3c0-1 1-2 2-2z"/>
    </symbol>
    <symbol id="icon-mail" viewBox="0 0 16 16">
      <path d="M1 3h14v10H1z M2.5 4.2 8 8.5l5.5-4.3z" fill-rule="evenodd"/>
    </symbol>
    <symbol id="icon-globe" viewBox="0 0 16 16">
      <path d="M8 1a7 7 0 1 0 0 14A7 7 0 0 0 8 1zm0 1.5c.9 1.2 1.5 3 1.6 5H6.4C6.5 5.5 7.1 3.7 8 2.5zM6.4 8.5h3.2c-.1 2-.7 3.8-1.6 5-.9-1.2-1.5-3-1.6-5z" fill-rule="evenodd"/>
    </symbol>
  </defs>
</svg>

<article class="card card--front">
  <div class="brand-mark"><span class="brand-mark__dot"></span>Rollers &amp; Glides</div>
  <section class="contact">
    <p class="contact__name">Marcus Pellow</p>
    <p class="contact__role">President</p>
    <div class="contact__rule"></div>
    <ul class="contact__list">
      <li class="contact__item"><svg class="contact__icon"><use href="#icon-phone"/></svg>480.915.2267</li>
      <li class="contact__item"><svg class="contact__icon"><use href="#icon-mail"/></svg>Marcus@rollersandglides-demo.com</li>
      <li class="contact__item"><svg class="contact__icon"><use href="#icon-globe"/></svg>www.rollersandglides-demo.com</li>
    </ul>
  </section>
  <p class="wordmark">Rollers &amp; Glides.com</p>
</article>

<article class="card card--back">
  <div class="brand-mark"><span class="brand-mark__dot"></span>Rollers &amp; Glides</div>
  <section class="contact">
    <p class="contact__name">Marcus Pellow</p>
    <p class="contact__role">President</p>
    <div class="contact__rule"></div>
    <ul class="contact__list">
      <li class="contact__item"><svg class="contact__icon"><use href="#icon-phone"/></svg>480.915.2267</li>
      <li class="contact__item"><svg class="contact__icon"><use href="#icon-mail"/></svg>Marcus@rollersandglides-demo.com</li>
      <li class="contact__item"><svg class="contact__icon"><use href="#icon-globe"/></svg>www.rollersandglides-demo.com</li>
    </ul>
  </section>
  <p class="wordmark">Rollers &amp; Glides.com</p>
</article>

</body>
</html>
```